Business card design

I already have the logo design completed and am requiring business card design and layout utilising the logo. I require a front and back design.

We are an executive recruitment company so we are looking at full colour, high finish in a reasonably conservative structure.

Reason: will be provide ai template

Target Market(s)

Senior Management 35-60 age bracket

Industry/Entity Type

Business

Requirements
Must have
• Peter Welling
• Director
• 238 Morrow Tce, Kelvin Grove QLD 4059
• Ph: 07 3628 4190 Mob: 0418527306
• peter@voltinapartners.com.au
• www.voltinapartners.com.au
Nice to have
• Ideally full colour,
Should not have
• cheap looking

```html
<!DOCTYPE html>
<html lang="en">
<head>
<meta charset="utf-8">
<title>Voltina Partners – Business Card</title>
<link rel="stylesheet" href="https://fonts.googleapis.com/css2?family=Montserrat:wght@700&family=Source+Sans+3:wght@400;700&display=swap">
<style>
  :root {
    --backdrop: #d2d3d5;
    --card-white: #ffffff;
    --navy: #143a6b;
    --navy-top: #0f4673;
    --navy-bottom: #13294f;
    --title-grey: #6b6b6b;
    --detail-grey: #a9a9a9;
    --white: #ffffff;
  }
  * { margin: 0; padding: 0; box-sizing: border-box; }
  html, body {
    width: 1200px;
    height: 848px;
    overflow: hidden;
    background: var(--backdrop);
  }
  .canvas {
    position: relative;
    width: 1200px;
    height: 848px;
  }
  .card {
    position: absolute;
    left: 356px;
    width: 487px;
    height: 271px;
  }
  .card--front {
    top: 125px;
    background: var(--card-white);
  }
  .card--back {
    top: 452px;
    background: linear-gradient(180deg, var(--navy-top) 0%, var(--navy-bottom) 100%);
  }

  .brand {
    position: absolute;
    display: flex;
    align-items: center;
    gap: 10px;
    font-family: "Montserrat", sans-serif;
    font-weight: 700;
    font-size: 22px;
    letter-spacing: 1.5px;
    white-space: nowrap;
  }
  .brand__mark {
    width: 34px;
    height: 34px;
    flex: none;
  }
  .brand--front {
    left: 39px;
    top: 46px;
    color: var(--navy);
  }
  .brand--front .brand__mark { background: var(--navy); }
  .brand--back {
    left: 0;
    right: 0;
    top: 117px;
    justify-content: center;
    color: var(--white);
  }
  .brand--back .brand__mark { background: var(--white); }

  .person {
    position: absolute;
    left: 38px;
    top: 148px;
    font-family: "Source Sans 3", sans-serif;
  }
  .person__name {
    font-weight: 700;
    font-size: 21px;
    line-height: 24px;
    color: var(--navy);
    letter-spacing: -0.2px;
  }
  .person__title {
    font-weight: 400;
    font-size: 16px;
    line-height: 20px;
    color: var(--title-grey);
    letter-spacing: 1.2px;
  }

  .contact {
    position: absolute;
    left: 292px;
    top: 150px;
    list-style: none;
    font-family: "Source Sans 3", sans-serif;
    font-size: 13px;
    line-height: 21.3px;
    color: var(--detail-grey);
    letter-spacing: 0.6px;
  }
  .contact__email { letter-spacing: 0.2px; font-size: 12.5px; }

  .website {
    position: absolute;
    left: 0;
    right: 0;
    top: 236px;
    text-align: center;
    font-family: "Source Sans 3", sans-serif;
    font-size: 15.5px;
    color: var(--white);
    letter-spacing: 1px;
  }
</style>
</head>
<body>
<main class="canvas">
  <section class="card card--front" aria-label="Business card front">
    <div class="brand brand--front">
      <span class="brand__mark" aria-hidden="true"></span>
      <span class="brand__name">VOLTINA PARTNERS</span>
    </div>
    <div class="person">
      <p class="person__name">Peter Welling</p>
      <p class="person__title">Director</p>
    </div>
    <ul class="contact">
      <li>xxxx xxxx xxxx</li>
      <li>xxxx xxxx</li>
      <li>P:(555) 555-5555</li>
      <li>F:(555) 555-5555</li>
      <li class="contact__email">peter@voltinapartners.com.au</li>
    </ul>
  </section>

  <section class="card card--back" aria-label="Business card back">
    <div class="brand brand--back">
      <span class="brand__mark" aria-hidden="true"></span>
      <span class="brand__name">VOLTINA PARTNERS</span>
    </div>
    <p class="website">www.voltinapartners.com.au</p>
  </section>
</main>
</body>
</html>
```